Business Card Design

I already have a company logo for my company. I have a logo for the manufacturer we represent. I want a professional business card design.

```html
<!DOCTYPE html>
<html lang="en">
<head>
<meta charset="utf-8">
<title>Beacon Alert Group – Business Card</title>
<link rel="stylesheet" href="https://fonts.googleapis.com/css2?family=Open+Sans:wght@400;600;700&display=swap">
<style>
  :root {
    --backdrop: #4a4a4a;
    --card: #161616;
    --edge: #e0ae1e;
    --red: #e31e26;
    --white: #f2f2f2;
    --muted: #d9d9d9;
  }
  * { box-sizing: border-box; margin: 0; padding: 0; }
  html, body {
    width: 1200px; height: 801px; overflow: hidden;
    background: radial-gradient(ellipse at 40% 30%, #585858, var(--backdrop) 60%, #3c3c3c);
    font-family: "Open Sans", Arial, sans-serif;
  }
  .sheet {
    position: relative; width: 1200px; height: 801px;
    display: flex; align-items: center; justify-content: center; gap: 40px;
  }
  .card {
    position: relative; width: 540px; height: 309px;
    background: var(--card);
    border-radius: 16px;
    border: 2px solid var(--edge);
    overflow: hidden;
    box-shadow: 0 18px 40px rgba(0,0,0,.45);
  }

  /* Front: contact side */
  .brand {
    position: absolute; left: 44px; top: 52px;
    display: flex; align-items: center; gap: 10px;
    color: var(--white); font-weight: 700; font-size: 22px; line-height: 1.1;
    width: 200px;
  }
  .brand-dot { flex: none; width: 18px; height: 18px; border-radius: 50%; background: var(--red); }
  .divider {
    position: absolute; left: 272px; top: 48px; width: 1.5px; height: 140px;
    background: var(--red);
  }
  .contacts {
    position: absolute; left: 296px; top: 66px;
    list-style: none; color: var(--white); font-size: 14px;
  }
  .contacts li { display: flex; align-items: center; gap: 10px; margin-bottom: 12px; }
  .contacts svg { width: 14px; height: 14px; fill: var(--red); flex: none; }
  .person { position: absolute; left: 44px; top: 150px; }
  .person-name { color: var(--red); font-weight: 600; font-size: 24px; letter-spacing: .5px; }
  .person-role { color: var(--muted); font-size: 15px; margin-top: 2px; }
  .address-band {
    position: absolute; left: 0; right: 0; bottom: 22px; height: 34px;
    background: var(--red);
    display: flex; align-items: center; justify-content: center;
    color: var(--white); font-size: 15px;
  }
  .band-dot {
    position: absolute; right: 18px; top: 9px;
    width: 16px; height: 16px; border-radius: 50%; background: var(--white);
  }

  /* Back: brand side */
  .card-back { display: flex; align-items: center; justify-content: center; }
  .brand-large {
    display: flex; align-items: center; gap: 16px;
    color: var(--white); font-weight: 700; font-size: 38px; line-height: 1.1;
  }
  .brand-large .brand-dot { width: 34px; height: 34px; }
</style>
</head>
<body>
<main class="sheet">
  <section class="card card-front">
    <div class="brand"><span class="brand-dot"></span><span>Beacon Alert Group</span></div>
    <div class="divider"></div>
    <ul class="contacts">
      <li><svg viewBox="0 0 24 24"><path d="M6.6 10.8a15.1 15.1 0 0 0 6.6 6.6l2.2-2.2a1 1 0 0 1 1-.25 11.4 11.4 0 0 0 3.6.57 1 1 0 0 1 1 1V20a1 1 0 0 1-1 1A17 17 0 0 1 3 4a1 1 0 0 1 1-1h3.5a1 1 0 0 1 1 1c0 1.25.2 2.45.57 3.57a1 1 0 0 1-.25 1z"/></svg>123 456 789</li>
      <li><svg viewBox="0 0 24 24"><path d="M2 5h20v14H2zm2 2v.5l8 5 8-5V7zm0 2.8V17h16V9.8l-8 5z"/></svg>info@yourgmail.com</li>
      <li><svg viewBox="0 0 24 24"><path d="M12 2a10 10 0 1 0 0 20 10 10 0 0 0 0-20zm0 2c1 1.2 1.8 3 2.1 5H9.9C10.2 7 11 5.2 12 4zM4.3 11h3.6a16 16 0 0 0 .3 3H4.7a8 8 0 0 1-.4-3zm5.6 0h4.2a14 14 0 0 1-.3 3h-3.6a14 14 0 0 1-.3-3zm6.2 0h3.6a8 8 0 0 1-.4 3h-3.5a16 16 0 0 0 .3-3z"/></svg>www.yourwebsite.com</li>
    </ul>
    <div class="person">
      <p class="person-name">DANIEL REYES</p>
      <p class="person-role">Managing Director</p>
    </div>
    <div class="address-band">Your address, City State, Zip 1234<span class="band-dot"></span></div>
  </section>

  <section class="card card-back">
    <div class="brand-large"><span class="brand-dot"></span><span>Beacon Alert Group</span></div>
  </section>
</main>
</body>
</html>
```